real esate business card with company logo and name

we need a business card design for a real esate company

The company name is Walsh & Brand Pty Ltd, and we have our logo designed and will upload. We want classic or moden feel. Black or white background. looks more textured. Should include folowinginformations
Owen Walsh and Lucy Brand
Sales Agents & Onsite Manager
p: 07 5948 2063
F: 07 5948 2174
M:0431 857 219
3/42 Marlow Crescent, FERNLEA QLD 4213

We want this business card looks professonal. Thank you in advance.

Industry/Entity Type

Real Estate Agent

Contact Information for Business Card

Owen Walsh and Lucy Brand
Onsite Manager & Sales Agents
p: 07 5948 2063
M:0431 857 219

Font styles to use
Serif

Colors
000000
fbfbfb
333333
959595

Requirements
Must have
• company logo and name, black or white back ground

```html
<!DOCTYPE html>
<html lang="en">
<head>
<meta charset="utf-8">
<title>Walsh &amp; Brand Pty Ltd – Business Card</title>
<link rel="stylesheet" href="https://fonts.googleapis.com/css2?family=Open+Sans:wght@400;600&display=swap">
<style>
  :root {
    --page-bg: #e9e9e9;
    --card-white: #fbfbfb;
    --band-light: #959595;
    --band-dark: #333333;
    --ink-light: #ffffff;
    --brand-grey: #7a7a7a;
    --shadow: rgba(0, 0, 0, 0.25);
  }
  * { margin: 0; padding: 0; box-sizing: border-box; }
  html, body {
    width: 1200px;
    height: 800px;
    overflow: hidden;
    background: var(--page-bg);
    font-family: "Open Sans", Arial, sans-serif;
  }
  .stage {
    position: relative;
    width: 1200px;
    height: 800px;
  }
  .business-card {
    position: absolute;
    left: 150px;
    top: 125px;
    width: 900px;
    height: 550px;
    background: var(--card-white);
    box-shadow: 0 14px 36px var(--shadow);
    overflow: hidden;
  }
  .card-band {
    position: absolute;
    inset: 0;
    width: 900px;
    height: 550px;
  }
  .band-light { fill: var(--band-light); }
  .band-dark { fill: var(--band-dark); }

  .brand {
    position: absolute;
    left: 0;
    right: 0;
    top: 130px;
    display: flex;
    justify-content: center;
    align-items: center;
    gap: 16px;
    padding-left: 180px;
  }
  .brand-mark {
    width: 34px;
    height: 34px;
    background: var(--brand-grey);
  }
  .brand-name {
    font-size: 26px;
    font-weight: 600;
    letter-spacing: 2px;
    text-transform: uppercase;
    color: var(--brand-grey);
  }

  .contact {
    position: absolute;
    left: 0;
    right: 0;
    top: 335px;
    padding-left: 150px;
    text-align: center;
    color: var(--ink-light);
  }
  .contact-names {
    font-size: 36px;
    font-weight: 400;
    letter-spacing: 1px;
    line-height: 1.1;
  }
  .contact-role {
    font-size: 25px;
    letter-spacing: 1px;
    line-height: 1.2;
  }
  .contact-phones {
    margin-top: 14px;
    font-size: 24px;
    font-weight: 600;
    letter-spacing: 1px;
    display: flex;
    justify-content: center;
    align-items: center;
    gap: 12px;
  }
  .phone-icon {
    width: 20px;
    height: 20px;
    fill: var(--ink-light);
  }
  .phone-divider {
    width: 1px;
    height: 30px;
    background: var(--ink-light);
    margin: 0 6px;
  }
  .contact-address {
    margin-top: 6px;
    font-size: 24px;
    font-weight: 600;
    letter-spacing: 1px;
  }
</style>
</head>
<body>
<main class="stage">
  <section class="business-card" aria-label="Walsh &amp; Brand business card">
    <svg class="card-band" viewBox="0 0 900 550" aria-hidden="true">
      <path class="band-light" d="M0 235 C 250 250, 600 300, 900 330 L900 550 L0 550 Z"/>
      <path class="band-dark" d="M0 258 C 250 272, 600 322, 900 352 L900 550 L0 550 Z"/>
    </svg>

    <div class="brand">
      <span class="brand-mark" aria-hidden="true"></span>
      <span class="brand-name">Walsh &amp; Brand Pty Ltd.</span>
    </div>

    <div class="contact">
      <p class="contact-names">Owen Walsh and Lucy Brand</p>
      <p class="contact-role">Onsite Manager &amp; Sales Agents</p>
      <p class="contact-phones">
        <span>0431 857 219</span>
        <svg class="phone-icon" viewBox="0 0 20 20" aria-label="mobile">
          <rect x="0" y="0" width="20" height="20" rx="2"/>
          <rect x="6" y="3" width="8" height="14" rx="1.5" fill="#333333"/>
          <rect x="7.5" y="5" width="5" height="8" fill="#ffffff"/>
        </svg>
        <span class="phone-divider" aria-hidden="true"></span>
        <svg class="phone-icon" viewBox="0 0 20 20" aria-label="phone">
          <rect x="0" y="0" width="20" height="20" rx="2"/>
          <path d="M6 4 L8.5 4 L9.5 7 L8 8.2 C8.8 10 10 11.2 11.8 12 L13 10.5 L16 11.5 L16 14 C10 15 5 10 6 4 Z" fill="#333333"/>
        </svg>
        <span>07 5948 2063</span>
      </p>
      <p class="contact-address">3/42 Marlow Crescent, FERNLEA QLD 4213</p>
    </div>
  </section>
</main>
</body>
</html>
```